Cyber Security firm working in the Financial Services sector needs a brochure

We need a brochure covering our products and offerings. We work exclusively with Independent Broker Dealers, their Reps and RIAs in the US. We help them keep their computers secure and compliant with applicable regulations and policies. Have attached samples of our logo an descriptions of our products and services.

Target Market(s)

Financial Institutions and Financial Advisors

Industry/Entity Type

Financial Service

```html
<!DOCTYPE html>
<html lang="en">
<head>
<meta charset="utf-8">
<title>Cyber Security Solutions Brochure</title>
<link rel="stylesheet" href="https://fonts.googleapis.com/css2?family=Source+Sans+3:wght@400;600;700&display=swap">
<style>
  :root {
    --bg: #e6e7e9;
    --blue-deep: #1a3f93;
    --blue-mid: #1f66c4;
    --blue-bright: #19a2e3;
    --panel: #d2d8de;
    --heading: #1d4b9e;
    --body-dark: #3d4a59;
    --white: #ffffff;
  }
  * { box-sizing: border-box; margin: 0; padding: 0; }
  html, body { width: 1200px; height: 960px; overflow: hidden; background: var(--bg); }
  body { font-family: "Source Sans 3", Arial, sans-serif; position: relative; }

  .brochure {
    position: absolute; left: 250px; top: 27px; width: 700px; height: 906px;
    background: var(--panel); overflow: hidden;
  }
  .header-band {
    position: absolute; left: 0; top: 0; width: 700px; height: 232px;
    background: linear-gradient(100deg, var(--blue-deep) 0%, var(--blue-mid) 55%, var(--blue-bright) 100%);
    padding: 56px 44px 0 44px; color: var(--white);
  }
  .title { font-size: 38px; font-weight: 700; letter-spacing: 0.5px; line-height: 1; }
  .intro { margin-top: 16px; font-size: 13px; font-weight: 600; line-height: 1.4; max-width: 610px; }

  .side-column {
    position: absolute; left: 0; top: 232px; width: 282px; height: 674px;
    background: linear-gradient(160deg, var(--blue-mid) 0%, var(--blue-deep) 45%, var(--blue-mid) 80%, var(--blue-bright) 100%);
    color: var(--white);
  }
  .hero-photo {
    width: 282px; height: 196px;
    background: linear-gradient(135deg, #c7d3df 0%, #6f86a3 40%, #2c3f5c 100%);
  }
  .side-section { padding: 24px 30px 0 34px; }
  .side-section h2 { font-size: 17px; font-weight: 700; text-transform: uppercase; line-height: 1.1; margin-bottom: 10px; }
  .side-section p { font-size: 10.5px; line-height: 1.45; }

  .main-column {
    position: absolute; left: 282px; top: 232px; width: 418px; height: 674px;
    padding: 0 30px 22px; display: flex; flex-direction: column;
  }
  .service { padding: 18px 0 14px; border-bottom: 2px solid var(--heading); position: relative; }
  .service h2 { color: var(--heading); font-size: 17px; font-weight: 700; text-transform: uppercase; line-height: 1.1; margin-bottom: 8px; }
  .service p { color: var(--body-dark); font-size: 10.5px; line-height: 1.42; }
  .service--patching { padding-top: 0; padding-bottom: 12px; }
  .service--patching h2 { width: 200px; margin-top: 0; }
  .patching-head { display: flex; justify-content: space-between; align-items: flex-end; margin-right: -30px; margin-bottom: 8px; }
  .patching-head h2 { margin-bottom: 0; }
  .desk-photo {
    width: 150px; height: 70px; flex: none;
    background: linear-gradient(135deg, #f4f6f9 0%, #c9d2dc 60%, #a7b4c3 100%);
  }

  .footer { margin-top: auto; display: flex; justify-content: space-between; align-items: flex-end; }
  .contact { font-size: 11.5px; font-weight: 700; color: #111; line-height: 1.35; }
  .brand { display: flex; align-items: center; gap: 6px; color: var(--heading); font-size: 17px; font-weight: 700; }
  .brand-dot { width: 10px; height: 10px; border-radius: 50%; background: var(--heading); }
</style>
</head>
<body>
  <article class="brochure">
    <header class="header-band">
      <h1 class="title">CYBER SECURITY SOLUTIONS</h1>
      <p class="intro">Vaultline Secure provides Computer Security support and services to the Broker Dealer and Independent Advisor community. We have been providing these services for over eight years and our team has decades of experience in the Financial Services sector. We currently support, monitor and inspect thousands of Advisors and their devices across multiple Broker Dealers and RIAs. Below is a list of our most popular services.</p>
    </header>

    <aside class="side-column">
      <div class="hero-photo" role="img" aria-label="Photo of a businessman in a suit touching a glowing padlock icon over streams of binary code"></div>
      <section class="side-section">
        <h2>Whole Disk Encryption</h2>
        <p>We remotely access your computer and perform whole disk encryption as required by your Broker Dealer. We can also help you select the most appropriate encryption methodology for your specific environment. Pricing from $95 per computer.</p>
      </section>
      <section class="side-section">
        <h2>Computer Security<br>Monitoring</h2>
        <p>We monitor the security status of your computer on a daily basis. We detect if any new software was installed and if it appears to be dangerous we contact you to discuss the ramifications. We monitor the security patch levels of key software and compare your status to that required by your BD. If there are security fixes available for your computer, we provide you with the necessary information and help get those applied. We also check the status of your anti-virus and disk encryption to make sure it is within guidelines. Pricing $8 per computer per month.</p>
      </section>
    </aside>

    <main class="main-column">
      <section class="service">
        <h2>Managed Backup</h2>
        <p>We partner with Halden owned Strata Backup Pro to provide backup services. This provides encrypted transmission and storage in SSAE 16 audited and ISO 27001 certified facilities for your back-up needs. We help you configure the back-ups, monitor them on a daily basis and are there to help if you need to do any restores. Price $1 per GB per month.</p>
      </section>
      <section class="service">
        <h2>Managed Anti-Virus</h2>
        <p>Correctly functioning and up-to-date Anti-Virus (AV) software is a requirement for all computers connected to the internet. With only one or two computers it is relatively easy to stay on top of the situation. However, once you get more than a couple of computers and users knowing their condition becomes more difficult without centralized reporting and monitoring. Our managed AV solution provides a centralized portal for monitoring and reporting. We are notified of any issues, whether it's a virus detected or an issue with the AV itself. This software and service is available for $52 per user per year with a one time set up fee or $25 per device. The advantage of the per user fee is, if a user has both a desktop and a laptop, both will be covered for the $52 per year.</p>
      </section>
      <section class="service service--patching">
        <div class="patching-head">
          <h2>Managed Software Patching</h2>
          <div class="desk-photo" role="img" aria-label="Photo of hands typing on a laptop at a bright office desk"></div>
        </div>
        <p>Keeping computers up-to-date with all critical security patches is an important component in protecting your infrastructure. An effective Patch Management strategy requires timely application of patches. Our patching functions in a closed loop environment. We push the necessary patches to the computers and then use our monitoring system at the device level to verify all have been successfully applied. This solution is quite effective for distributed environments with limited local cyber security expertise as well as small offices which prefer to outsource this requirement. Price $3.99 per month per computer. Requires Computer Security Monitoring.</p>
      </section>
      <footer class="footer">
        <div class="contact">
          Phone: 555-014-2290<br>
          Email: info@vaultlinesecure.com<br>
          www.vaultlinesecure.com
        </div>
        <div class="brand"><span class="brand-dot"></span>Vaultline Secure</div>
      </footer>
    </main>
  </article>
</body>
</html>
```